Crumb of Maple 2022- CW poster ads

Design for our Crumb of Maple Event
Designs 3 designs for Chirp Wall Banner, posts and social Media ads
Each can look the same just different subjects on each
1. Design We're Back!
The Crumb Of Maple Is Back!
Ventura County’s Premier Food, Wine and Brew Event
August 14th
Vendor and ticket info at https://brimfulmaplefq.com/

2. Vendors be a part of the event
The Crumb of Maple is Back!
August 14th 2020
Vendors sign up today at
Vendor info at https://brimfulmaplefq.com/

3. Sponsor info
The Crumb Of Maple
August 14th 2022
Check out our great Sponsorship opportunities
Sponsor info at https://brimfulmaplefq.com/

Target Market(s)

Foodies, wine and beer enthusists

Industry/Entity Type

Farm to fork, fresh in season and local

Colors
00AB8E
00BBA5
67D7C9
C6EFE9
E9F9F6

Requirements
Should not have
• no fast food looking photos

```html
<!DOCTYPE html>
<html lang="en">
<head>
<meta charset="utf-8">
<title>The Crumb Of Maple Is Back! – Banner</title>
<link href="https://fonts.googleapis.com/css2?family=Lobster&display=swap" rel="stylesheet">
<style>
  :root {
    --stage: #8a8a8a;
    --parchment-light: #f3e2b4;
    --parchment-mid: #e8c987;
    --parchment-dark: #d7ad62;
    --brand-green: #00ab8e;
    --headline-brown: #7a4836;
    --frame-brown: #8a4d2c;
    --text-light: #ffffff;
  }
  html, body {
    margin: 0;
    width: 1200px;
    height: 944px;
    overflow: hidden;
    background: var(--stage);
  }
  .banner {
    position: absolute;
    left: 39px;
    top: 178px;
    width: 1122px;
    height: 588px;
    overflow: hidden;
    background: radial-gradient(ellipse at 40% 35%, var(--parchment-light) 0%, var(--parchment-mid) 60%, var(--parchment-dark) 100%);
    font-family: "Lobster", cursive;
  }
  .headline {
    position: absolute;
    left: 40px;
    top: 38px;
    width: 470px;
    margin: 0;
    color: var(--headline-brown);
    text-align: center;
    font-weight: 400;
    line-height: 1;
    text-shadow: 2px 3px 0 rgba(255,240,210,.6);
  }
  .headline .line-small { display: block; font-size: 52px; padding-left: 120px; }
  .headline .line-big { display: block; font-size: 116px; margin-top: -14px; }
  .headline .line-mid { display: block; font-size: 56px; margin-top: -6px; }
  .info-band {
    position: absolute;
    left: 0;
    top: 282px;
    width: 100%;
    height: 292px;
    background: var(--brand-green);
  }
  .event-copy {
    position: absolute;
    left: 80px;
    top: 318px;
    width: 420px;
    color: var(--text-light);
    text-shadow: 1px 2px 2px rgba(0,0,0,.25);
  }
  .event-copy p { margin: 0; line-height: 1.05; }
  .event-copy .tagline { font-size: 22px; }
  .event-copy .event-name { font-size: 41px; margin-top: 12px; }
  .event-copy .event-date { font-size: 41px; text-align: center; }
  .event-copy .event-link { font-size: 25px; text-align: right; margin-top: 16px; }
  .photo-frame {
    position: absolute;
    left: 522px;
    top: 142px;
    width: 575px;
    height: 395px;
  }
  .brand-name {
    position: absolute;
    left: 522px;
    top: 70px;
    width: 575px;
    display: flex;
    justify-content: center;
    align-items: center;
    gap: 12px;
    font-size: 36px;
    color: var(--headline-brown);
  }
  .brand-name .brand-dot {
    width: 18px;
    height: 18px;
    border-radius: 50%;
    background: var(--brand-green);
  }
</style>
</head>
<body>
  <main class="banner">
    <h1 class="headline">
      <span class="line-small">The</span>
      <span class="line-big">Crumb</span>
      <span class="line-mid">Of Maple Is Back!</span>
    </h1>

    <div class="info-band"></div>

    <section class="event-copy">
      <p class="tagline">Ventura County’s Premier Food,</p>
      <p class="event-name">Wine and Brew Event</p>
      <p class="event-date">August 14th</p>
      <p class="event-link">Vendor and ticket info<br>at https://brimfulmaplefq.com/</p>
    </section>

    <div class="brand-name"><span class="brand-dot"></span><span>Brimful Maple</span></div>

    <svg class="photo-frame" viewBox="0 0 575 395" role="img" aria-label="Photo of a plated dish: sliced roast pork with gravy and spinach risotto">
      <defs>
        <linearGradient id="dishTone" x1="0" y1="0" x2="1" y2="1">
          <stop offset="0" stop-color="#b98a66"/>
          <stop offset="0.45" stop-color="#8a5a3c"/>
          <stop offset="0.75" stop-color="#e6dcae"/>
          <stop offset="1" stop-color="#dfe6ec"/>
        </linearGradient>
      </defs>
      <path d="M40 12 H535 Q535 40 563 40 V355 Q535 355 535 383 H40 Q40 355 12 355 V40 Q40 40 40 12 Z" fill="var(--frame-brown)"/>
      <path d="M48 22 H527 Q530 48 553 50 V345 Q530 348 527 373 H48 Q45 348 22 345 V50 Q45 48 48 22 Z" fill="url(#dishTone)"/>
    </svg>
  </main>
</body>
</html>
```